Business Card Design

We need a business card designed for our new company. Prefer a black card with white logo & writing.

Contact Information for Business Card

Ted Galloway, address: 7-4812 Fernhollow Road, Abbotsford, BC, V3K 8R2, Office Phone: 604-712-3390, Cell: 604-947-2164, Email: ted@resinworkshub.ca

Colors

Designer to choose only greyscale colors for use in the design.

```html
<!DOCTYPE html>
<html lang="en">
<head>
<meta charset="utf-8">
<title>Resinworks Hub – Business Card</title>
<link rel="stylesheet" href="https://fonts.googleapis.com/css2?family=Montserrat:wght@400;600;700;800&display=swap">
<style>
  :root {
    --backdrop: #d8d6d3;
    --card: #2b2b2b;
    --card-edge: #232323;
    --ink: #ffffff;
    --ink-soft: #e6e6e6;
    --art-dark: #3a3a3a;
    --art-light: #e9e9e9;
  }
  * { box-sizing: border-box; margin: 0; padding: 0; }
  html, body {
    width: 900px;
    height: 1200px;
    overflow: hidden;
  }
  body {
    background: var(--backdrop);
    font-family: "Montserrat", Arial, sans-serif;
    color: var(--ink);
    position: relative;
  }
  .card {
    position: absolute;
    left: 79px;
    width: 743px;
    height: 442px;
    background: var(--card);
    border-radius: 22px;
    overflow: hidden;
    box-shadow: 0 10px 24px rgba(0,0,0,0.28);
  }
  .card--front { top: 131px; }
  .card--back { top: 638px; }

  .brand-name {
    position: absolute;
    font-weight: 800;
    color: var(--ink);
    letter-spacing: 0.5px;
    white-space: nowrap;
    text-transform: uppercase;
  }
  .card--front .brand-name {
    left: 27px;
    top: 92px;
    font-size: 27px;
  }
  .card--back .brand-name {
    left: 0;
    right: 0;
    top: 195px;
    text-align: center;
    font-size: 52px;
    letter-spacing: 1px;
  }

  .holder {
    position: absolute;
    right: 45px;
    top: 38px;
    text-align: right;
  }
  .holder__name {
    font-size: 23px;
    font-weight: 700;
    line-height: 1.2;
  }
  .holder__role {
    font-size: 14px;
    font-weight: 400;
    color: var(--ink-soft);
    margin-top: 4px;
  }

  .address {
    position: absolute;
    left: 40px;
    top: 234px;
    font-size: 15px;
    line-height: 20px;
    color: var(--ink-soft);
  }

  .contact-list {
    position: absolute;
    left: 37px;
    top: 297px;
    list-style: none;
  }
  .contact-list li {
    display: flex;
    align-items: center;
    height: 29px;
    font-size: 15px;
    color: var(--ink-soft);
  }
  .contact-list li:nth-child(3) { height: 26px; }
  .contact-list svg {
    width: 14px;
    height: 14px;
    margin-right: 14px;
    fill: var(--ink);
    flex: none;
  }

  .peak-art {
    position: absolute;
    left: 276px;
    top: 272px;
    width: 467px;
    height: 170px;
    background: linear-gradient(160deg, var(--card) 35%, var(--art-dark) 60%, var(--art-light) 100%);
    clip-path: polygon(0 88%, 49% 0, 100% 88%, 100% 100%, 0 100%);
    opacity: 0.55;
  }
</style>
</head>
<body>

  <section class="card card--front" aria-label="Card front">
    <div class="brand-name">Resinworks Hub</div>

    <div class="holder">
      <div class="holder__name">Ted Galloway</div>
      <div class="holder__role">owner</div>
    </div>

    <p class="address">7-4812 Fernhollow Road,<br>Abbotsford, BC, V3K 8R2</p>

    <ul class="contact-list">
      <li>
        <svg viewBox="0 0 24 24" aria-hidden="true"><path d="M6.6 10.8a15.1 15.1 0 0 0 6.6 6.6l2.2-2.2c.3-.3.7-.4 1-.2 1.1.4 2.3.6 3.6.6.6 0 1 .4 1 1V20c0 .6-.4 1-1 1A17 17 0 0 1 3 4c0-.6.4-1 1-1h3.5c.6 0 1 .4 1 1 0 1.3.2 2.5.6 3.6.1.3 0 .7-.2 1z"/></svg>
        604-712-3390
      </li>
      <li>
        <svg viewBox="0 0 24 24" aria-hidden="true"><path d="M7 1h10a2 2 0 0 1 2 2v18a2 2 0 0 1-2 2H7a2 2 0 0 1-2-2V3a2 2 0 0 1 2-2zm0 3v14h10V4zm5 15.2a1.2 1.2 0 1 0 0 2.4 1.2 1.2 0 0 0 0-2.4z"/></svg>
        604-947-2164
      </li>
      <li>
        <svg viewBox="0 0 24 24" aria-hidden="true"><path d="M2 5h20v2l-10 6L2 7zm0 4.3 10 6 10-6V19H2z"/></svg>
        ted@resinworkshub.ca
      </li>
      <li>
        <svg viewBox="0 0 24 24" aria-hidden="true"><path d="M12 2a10 10 0 1 0 0 20 10 10 0 0 0 0-20zm-1 17.9A8 8 0 0 1 4.1 10L9 15v1a2 2 0 0 0 2 2zm6.9-2.5A2 2 0 0 0 16 16h-1v-3a1 1 0 0 0-1-1H8v-2h2a1 1 0 0 0 1-1V7h2a2 2 0 0 0 2-2v-.4a8 8 0 0 1 2.9 12.8z"/></svg>
        www.resinworkshub.ca
      </li>
    </ul>

    <div class="peak-art" role="img" aria-label="White mountain peak silhouette rising from the lower right corner"></div>
  </section>

  <section class="card card--back" aria-label="Card back">
    <div class="brand-name">Resinworks Hub</div>
  </section>

</body>
</html>
```